Finding the Root: Reason in Clinical Choice-Crafting

I'd like a cover that looks like it would fit on the shelf next to "The Illness Mirage" by Corwin Talley, "The Close of Forgetting" by Hugh Marchetti, "Meal Mend" by Paul Grieve, "The Energy Restart Plan" by Oscar Pemberley or "The Gland Restart Plan" by the same or "The Cortex Restart Plan" by the same ... either text only (with some interesting fonts that make the title stand out, and the subtitle smaller) or a relevant image, though I'm not entirely sure what that would be since this is a book about big-picture medical decision making.
Author name is Dr Tessa Morrow, NMD
I'll eventually request an e-book, paperback, and audio cover from the winner...

Target Market(s)

practicing physicians

Industry/Entity Type

medicine

Requirements
Must have
• look similar to other books in the genre

```html
<!DOCTYPE html>
<html lang="en">
<head>
<meta charset="utf-8">
<title>Finding the Root – Book Cover</title>
<link rel="stylesheet" href="https://fonts.googleapis.com/css2?family=Bebas+Neue&family=Poppins:wght@600&display=swap">
<style>
  :root {
    --backdrop: #cfd2d3;
    --paper: #ffffff;
    --green: #97b518;
    --teal: #00a9b5;
    --yellow: #f0c800;
    --yellow-soft: #fbf1bf;
  }
  html, body {
    margin: 0;
    padding: 0;
    width: 1200px;
    height: 2615px;
    overflow: hidden;
    background: var(--backdrop);
  }
  .canvas {
    position: relative;
    width: 1200px;
    height: 2615px;
  }
  .cover {
    position: absolute;
    left: 50px;
    top: 481px;
    width: 1100px;
    height: 1652px;
    background: var(--paper);
  }
  .cover-art {
    position: absolute;
    left: 199px;
    top: 156px;
    width: 708px;
    height: 184px;
    border-radius: 92px;
    background: linear-gradient(90deg, var(--paper), var(--yellow-soft) 30%, var(--yellow-soft) 70%, var(--paper));
  }
  .title {
    position: absolute;
    left: 0;
    top: 383px;
    width: 100%;
    margin: 0;
    text-align: center;
    font-family: "Bebas Neue", "Oswald", sans-serif;
    font-weight: 400;
    font-size: 305px;
    line-height: 246px;
  }
  .title span { display: block; }
  .title-green { color: var(--green); }
  .title-teal { color: var(--teal); }
  .subtitle {
    position: absolute;
    left: 0;
    top: 1146px;
    width: 100%;
    margin: 0;
    text-align: center;
    font-family: "Bebas Neue", "Oswald", sans-serif;
    font-weight: 400;
    font-size: 80px;
    line-height: 75px;
    letter-spacing: 8px;
  }
  .subtitle span { display: block; }
  .subtitle-teal { color: var(--teal); }
  .subtitle-yellow { color: var(--yellow); }
  .author {
    position: absolute;
    left: 0;
    top: 1500px;
    width: 100%;
    margin: 0;
    text-align: center;
    font-family: "Poppins", "Helvetica", sans-serif;
    font-weight: 600;
    font-size: 34px;
    letter-spacing: 4px;
    color: var(--green);
  }
</style>
</head>
<body>
  <main class="canvas">
    <section class="cover">
      <div class="cover-art" role="img" aria-label="Thin yellow single-line drawing of a tangled brain leading to a crossroads of arrows"></div>
      <h1 class="title">
        <span class="title-green">Finding</span>
        <span class="title-green">The</span>
        <span class="title-teal">Root</span>
      </h1>
      <p class="subtitle">
        <span class="subtitle-teal">Reason in</span>
        <span class="subtitle-teal">Clinical</span>
        <span class="subtitle-yellow">Choice-Crafting</span>
      </p>
      <p class="author">DR TESSA MORROW, NMD</p>
    </section>
  </main>
</body>
</html>
```